redesign my website bluekeelvoyages.net and make it user friendly

I already have a website, bluekeelvoyages.net, and want a redesign in WordPress with Elementor Pro, using the same text/content. The goal is to improve:

Design quality (colors, fonts, spacing, visual flow)
User experience (easy navigation, clear offers)
Conversion readiness (calls-to-action, trust signals, booking flow)
Technical side (SEO basics, fast speed, full mobile responsiveness)

The site should look modern, clean, fun, engaging, interactive and optimized for speed and usability.

I would like the 11 page to be consolidate dto 6 as follows: Home (main landing, highlights)

Sailboat Trips (all packages, itineraries, pricing)
Boats (fleet details, features, photos)
How It Works (booking process, FAQs, travel info, what to expect)
Blog
Contact Us (form, WhatsApp, phone, etc.)

Target Market(s)

sailboat trip customers for San Blas Islands in Panama

Industry/Entity Type

Travel, Boat Tour Agency

Coding

Coded - Design and coding required

Number of Pages Required

3 page

Font styles to use
Sans Serif
Other font styles liked:
• Oswalg and sans serif

Colors
0054AA
0677BA
7BADD7
CADEEF
E8F1F8
0094D4
00A9DD
6FCCEA
C7EBF8
E9F6FB
FFC000
F8CF3A
FAE287
FDF2CF
FEFAEE
F0912C
F2A743
F7CA91
FBE8D2
FDF5EE

Requirements
Must have
• Home (main landing, highlights) Sailboat Trips (all packages, itineraries, pricing) Boats (fleet details, features, photos) How It Works (booking process, FAQs, travel info, what to expect) Blog (updates, travel tips, inspiration) Contact Us (form, WhatsApp, phone, etc.)
Nice to have
• I want it to look professionla and be very user friendy to entice people to contact me to book boat trips
Should not have
• a store

```html
<!DOCTYPE html>
<html lang="en">
<head>
<meta charset="utf-8">
<title>Blue Keel Voyages – San Blas Sailing</title>
<link href="https://fonts.googleapis.com/css2?family=Oswald:wght@500;600&family=Poppins:wght@400;500&display=swap" rel="stylesheet">
<style>
:root{
  --navy:#0054AA;
  --blue:#0677BA;
  --sky:#00A9DD;
  --pale:#E8F1F8;
  --gold:#FFC000;
  --gold2:#F8CF3A;
  --orange:#F2A743;
  --ink:#2b2b2b;
  --muted:#555;
  --footer:#2B56B4;
  --white:#fff;
}
*{box-sizing:border-box;margin:0;padding:0}
html,body{width:1200px;height:4152px;overflow:hidden}
body{position:relative;font-family:'Poppins',sans-serif;color:var(--ink);background:#fff}
.abs{position:absolute}
.oswald{font-family:'Oswald',sans-serif;text-transform:uppercase}

/* header + hero */
.hero{left:0;top:0;width:1200px;height:720px;background:linear-gradient(160deg,#c9a07a 0%,#4aa3c9 22%,#1a74b8 45%,#0c4f9a 75%,#0a3f86 100%)}
.hero-curve{left:0;top:640px;width:1200px;height:120px}
.brand{left:114px;top:22px;display:flex;align-items:center;gap:12px;color:#fff;font-weight:500;font-size:26px;white-space:nowrap}
.brand .dot{width:40px;height:40px;border-radius:50%;background:rgba(255,255,255,.85)}
.nav{left:447px;top:36px;width:753px;border-bottom:1px solid rgba(255,255,255,.8);padding-bottom:20px;display:flex;font-family:'Oswald',sans-serif;font-size:15px;color:#fff;white-space:nowrap}
.nav a{color:#fff;text-decoration:none;margin-left:10px;margin-right:28px}
.nav a.on{color:var(--gold)}
.menu-ico{left:1062px;top:36px;width:28px}
.menu-ico span{display:block;height:3px;background:#fff;margin-bottom:6px;border-radius:2px}
.menu-ico span:nth-child(2){width:20px}
.hero-title{left:0;top:158px;width:1200px;text-align:center;color:#fff;font-size:45px;line-height:62px;font-weight:500}
.hero-title em{font-style:normal;color:var(--gold)}
.btn{display:flex;align-items:center;justify-content:center;border-radius:30px;background:linear-gradient(90deg,var(--gold2),#f0b93a);color:#fff;font-family:'Oswald',sans-serif;font-size:15px;text-transform:uppercase;white-space:nowrap}
.hero-btn{left:514px;top:374px;width:171px;height:48px}

/* services */
.svc{top:665px;width:282px;height:334px;background:#fff;border-radius:14px;box-shadow:0 6px 18px rgba(0,0,0,.12);padding:36px 28px 0 29px;border-bottom:5px solid var(--gold2);overflow:hidden}
.svc .ico{width:84px;height:72px;border-radius:8px;background:linear-gradient(180deg,#2f8bd6,#1a6cc0);display:flex;align-items:center;justify-content:center}
.svc h3{font-weight:400;font-size:17px;margin:30px 0 12px}
.svc p{font-size:11.5px;line-height:20.5px;color:var(--muted)}

/* fleet */
.fleet{left:0;top:1089px;width:1200px;height:860px;background:linear-gradient(135deg,#1d5f6e,#1a4c60 50%,#184357)}
.fleet-curve{left:0;top:1850px;width:1200px;height:100px}
.fleet-title{left:0;top:1180px;width:1200px;text-align:center;color:#fff;font-size:38px;font-weight:500}
.fleet-title em,.sec-title em{font-style:normal;color:var(--gold)}
.boat{top:1282px;width:327px;height:455px;background:#fff;border-radius:14px;padding:15px;text-align:center;border-bottom:6px solid var(--sky)}
.boat .photo{width:297px;height:194px;border-radius:12px}
.boat h4{font-weight:400;color:var(--blue);font-size:21px;margin:20px 0 10px}
.boat .type{color:var(--orange);font-size:13px;letter-spacing:.5px}
.boat p{font-size:12px;line-height:21px;color:var(--muted);margin:10px 8px 0;height:63px;overflow:hidden}
.boat .specs{border-top:1px solid #ddd;margin:14px -15px 0;padding-top:14px;display:flex;justify-content:space-around;font-size:12px;color:var(--ink)}
.boat .specs span::before{content:"";display:inline-block;width:12px;height:14px;background:var(--navy);border-radius:2px;margin-right:7px;vertical-align:-2px}
.fleet-btn{left:483px;top:1783px;width:233px;height:48px}

/* testimonials */
.sec-title{left:0;width:1200px;text-align:center;font-size:38px;font-weight:500;color:var(--ink)}
.sec-title.blue em{color:var(--blue)}
.review-photo{left:111px;top:2149px;width:461px;height:382px;border-radius:16px;border:3px solid var(--gold2);background:linear-gradient(180deg,#8fb2cf,#4f7e9b 55%,#2d5c70)}
.review{left:599px;top:2164px;width:490px}
.stars{color:var(--gold);font-size:20px;letter-spacing:3px}
.review p{font-size:12.8px;line-height:30px;color:var(--muted);margin-top:10px}
.review .who{color:var(--blue);font-weight:500;font-size:18px;margin-top:12px}
.progress{left:333px;top:2598px;width:532px;height:6px;background:var(--pale);border-radius:3px}
.progress i{display:block;width:130px;height:6px;background:var(--gold2);border-radius:3px}

/* contact */
.contact-bg{left:0;top:2640px;width:1200px;height:1120px;background:linear-gradient(180deg,#1e57c0 0%,#3b87d8 40%,#6ec8e6 75%,#43c4df 100%)}
.contact-curve{left:0;top:2620px;width:1200px;height:120px}
.form-panel{left:113px;top:2830px;width:979px;height:827px;border-radius:14px;background:rgba(255,255,255,.9)}
.field{height:62px;background:#fff;border-radius:6px;box-shadow:0 3px 8px rgba(0,0,0,.1);font-size:12.5px;color:#444;padding:0 29px;display:flex;align-items:center;text-transform:uppercase;white-space:nowrap}
.field.msg{align-items:flex-start;padding-top:22px;height:148px}
.submit{left:527px;top:3558px;width:147px;height:50px;font-family:'Poppins',sans-serif;font-size:14px}

/* footer */
.footer{left:0;top:3758px;width:1200px;height:394px;background:var(--footer);color:#fff}
.footer::after{content:"";position:absolute;left:0;bottom:0;width:1200px;height:8px;background:var(--gold2)}
.f-brand{left:114px;top:3858px;width:220px;font-size:15px;line-height:26px;color:#fff}
.f-brand .mark{font-size:18px;font-weight:500;margin-bottom:14px;display:flex;align-items:center;gap:10px;white-space:nowrap}
.f-brand .mark i{width:16px;height:16px;border-radius:50%;background:var(--gold2)}
.f-col{top:3812px;font-size:15px;line-height:32.5px;color:#fff}
.f-col h5{color:var(--gold2);font-weight:500;font-size:18px;margin-bottom:6px;line-height:32px}
.f-col .row{display:flex;align-items:center;gap:9px;white-space:nowrap}
.f-col .circ{width:20px;height:20px;border-radius:50%;background:var(--gold2);display:inline-block}
.socials{display:flex;gap:8px;margin-top:8px}
.socials i{width:22px;height:22px;border-radius:50%;background:var(--gold2)}
.copy{left:0;top:4112px;width:1200px;text-align:center;font-size:13px;color:#fff}
.copy-line{left:0;top:4098px;width:1200px;height:1px;background:rgba(255,255,255,.25)}
</style>
</head>
<body>

<!-- HERO -->
<div class="abs hero" role="img" aria-label="Luxury yacht cruising turquoise sea beside a desert coastline"></div>
<svg class="abs hero-curve" viewBox="0 0 1200 120" preserveAspectRatio="none">
  <path d="M0 70 C300 20 700 40 1200 20 L1200 120 L0 120 Z" fill="#fff"/>
  <path d="M0 70 C300 20 700 40 1200 20" fill="none" stroke="#F8CF3A" stroke-width="8"/>
</svg>

<div class="abs brand"><span class="dot"></span>Blue Keel Voyages</div>
<nav class="abs nav">
  <a class="on">HOME</a><a>GUNA YALA</a><a>FLEET</a><a>ABOUT US</a><a>BOOK NOW</a><a>PRICING</a><a>ITINERARIES</a>
</nav>
<div class="abs menu-ico"><span></span><span></span><span></span></div>

<h1 class="abs hero-title oswald">San Blas <em>Islands</em><br>Panama Sailing Vacations<br>Ultimate Beaches &amp; Catamaran Tours</h1>
<a class="abs btn hero-btn">Inquire Now</a>

<!-- SERVICES -->
<div class="abs svc" style="left:147px">
  <div class="ico"><svg width="44" height="30" viewBox="0 0 44 30" fill="none" stroke="#fff" stroke-width="2"><path d="M2 18h40l-6 9H8z"/><path d="M10 18v-7h20l6 7"/><path d="M16 11V5h10v6"/></svg></div>
  <h3>Private Charters</h3>
  <p>Sail the beautiful islands and beaches of San Blas on a private all-inclusive catamaran. Enjoy a custom itinerary, friendly crew, and flexible options to fit any budget—perfect for a relaxing escape.</p>
</div>
<div class="abs svc" style="left:458px">
  <div class="ico"><svg width="44" height="34" viewBox="0 0 44 34" fill="none" stroke="#fff" stroke-width="2"><path d="M4 20h36l-5 7H9z"/><path d="M10 20v-6h22l5 6"/><path d="M16 14V8h10v6"/><path d="M2 31c4-3 8 3 12 0s8 3 12 0 8 3 12 0"/></svg></div>
  <h3>Shared Charters</h3>
  <p>Share the experience with others for a more affordable alternative to a private charter. Perfect for couples, solo travelers, and small groups—enjoy San Blas beaches, clear waters, great meals, and a relaxed atmosphere with a</p>
</div>
<div class="abs svc" style="left:768px">
  <div class="ico"><svg width="40" height="40" viewBox="0 0 40 40" fill="none" stroke="#fff" stroke-width="2"><path d="M20 3v6"/><path d="M13 9h14v8H13z"/><path d="M6 17h28l-4 10H10z"/><path d="M2 33c4-3 8 3 12 0s8 3 12 0 8 3 12 0"/></svg></div>
  <h3>Family Friendly Boat Trips</h3>
  <p>San Blas is perfect for kids, with calm waters, safe snorkeling, and fun island-hopping. Families love the mix of adventure and culture—an ideal way to explore Panama together.</p>
</div>

<!-- FLEET -->
<div class="abs fleet" role="img" aria-label="Aerial view of a boat wake across deep teal water"></div>
<svg class="abs fleet-curve" viewBox="0 0 1200 100" preserveAspectRatio="none">
  <path d="M0 22 C400 90 800 80 1200 20 L1200 100 L0 100 Z" fill="#fff"/>
  <path d="M0 22 C400 90 800 80 1200 20" fill="none" stroke="#F8CF3A" stroke-width="14"/>
</svg>
<h2 class="abs fleet-title oswald">Featured <em>Catamarans</em></h2>

<div class="abs boat" style="left:85px;border-bottom-color:var(--gold2)">
  <div class="photo" role="img" aria-label="Catamaran anchored off a white sand island" style="background:linear-gradient(180deg,#d9d2b8,#47bcc4 40%,#1a6f8e)"></div>
  <h4>Marina 42</h4><div class="type">CATAMARAN</div>
  <p>Service that exceeds all expectations! "We started as strangers and left as friends! The crew made sure everyone</p>
  <div class="specs"><span>42 FT</span><span>3 Cabin</span><span>8 Guest</span></div>
</div>
<div class="abs boat" style="left:438px">
  <div class="photo" role="img" aria-label="Catamaran moored in turquoise shallows near palm trees" style="background:linear-gradient(180deg,#5d8a5a,#5cc7c2 40%,#2a8ea6)"></div>
  <h4>Coral 55F</h4><div class="type">CATAMARAN</div>
  <p>Luxury and elegance on water! "It was like having our own private island, but with the luxury of a floating home.</p>
  <div class="specs"><span>42 FT</span><span>3 Cabin</span><span>8 Guest</span></div>
</div>
<div class="abs boat" style="left:791px">
  <div class="photo" role="img" aria-label="Sailing catamaran with guests on deck in open water" style="background:linear-gradient(180deg,#8fc3dd,#2f8fc0 50%,#1c6a9c)"></div>
  <h4>Coral 55S</h4><div class="type">CATAMARAN</div>
  <p>Safest family fun at sea! "The best family trip we've ever had! Our kids couldn't get enough of exploring the</p>
  <div class="specs"><span>42 FT</span><span>3 Cabin</span><span>8 Guest</span></div>
</div>
<a class="abs btn fleet-btn">See All Boats &amp; Prices</a>

<!-- TESTIMONIALS -->
<h2 class="abs sec-title blue oswald" style="top:2030px">What Our Guests <em>Say</em></h2>
<div class="abs review-photo" role="img" aria-label="Three guests swimming beside a catamaran"></div>
<div class="abs review">
  <div class="stars">★★★★★</div>
  <p>"Everything was absolutely great — from the transfer to the boat crew, the food, and the islands we visited. We really enjoyed the whole experience. The only thing we regret is not having more time to extend the trip in San Blas. We booked the Tortuga, the boat is spacious and very confortable. The captain Andres and the chef Marta. Were very professional, friendly and have a lot of knowledge of the San Blas and sailing. They took good care of us and made the trip even better. Chef Marta cooked amazing food! Thanks again for the great organization, and we definitely hope to come back in the future!"</p>
  <div class="who">– Markus, Germany</div>
</div>
<div class="abs progress"><i></i></div>

<!-- CONTACT -->
<div class="abs contact-bg" role="img" aria-label="Bright sky over a rocky coast and clear turquoise water"></div>
<svg class="abs contact-curve" viewBox="0 0 1200 120" preserveAspectRatio="none">
  <path d="M0 0 L1200 0 L1200 40 C800 90 400 80 0 20 Z" fill="#fff"/>
  <path d="M0 20 C400 80 800 90 1200 40" fill="none" stroke="#F8CF3A" stroke-width="12"/>
</svg>
<div class="abs form-panel"></div>
<h2 class="abs sec-title blue oswald" style="top:2900px;color:#222">Start Your San Blas <em>Adventure</em></h2>

<div class="abs field" style="left:187px;top:3006px;width:395px">Name</div>
<div class="abs field" style="left:612px;top:3006px;width:396px">Email</div>
<div class="abs field" style="left:187px;top:3096px;width:395px">Mobile Number</div>
<div class="abs field" style="left:612px;top:3096px;width:396px">No of Passengers</div>
<div class="abs field" style="left:187px;top:3186px;width:395px">No of Days</div>
<div class="abs field" style="left:612px;top:3186px;width:396px">Date</div>
<div class="abs field" style="left:187px;top:3277px;width:821px;justify-content:space-between">What type of experience are you looking for? (Check all that apply)
  <svg width="16" height="10" viewBox="0 0 16 10"><path d="M2 2l6 6 6-6" fill="none" stroke="#333" stroke-width="2"/></svg></div>
<div class="abs field msg" style="left:189px;top:3364px;width:821px">Message</div>
<a class="abs btn submit">SUBMIT</a>

<!-- FOOTER -->
<footer class="abs footer"></footer>
<div class="abs f-brand">
  <div class="mark"><i></i>Blue Keel Voyages</div>
  Discover unforgettable catamaran and sailboat adventures in Guna Yala (San Blas), Panama.
</div>
<div class="abs f-col" style="left:413px">
  <h5>QUICK LINKS</h5>Home<br>Guna Yala<br>Fleet<br>About Us<br>Book Now<br>Pricing
</div>
<div class="abs f-col" style="left:599px">
  <h5>QUICK LINKS</h5>Itineraries<br>Activities<br>Blog<br>FAQs<br>Contact Us<br>Prices for everyone
</div>
<div class="abs f-col" style="left:843px">
  <h5>GET IN TOUCH</h5>
  <div class="row"><span class="circ"></span>+507 6000 4120</div>
  <div class="row"><span class="circ"></span>hello@bluekeelvoyages.net</div>
  <div class="socials"><i></i><i></i><i></i></div>
  <div style="font-size:14px">EN ⌄</div>
</div>
<div class="abs copy-line"></div>
<div class="abs copy">Copyright 2022 © Blue Keel Voyages</div>

</body>
</html>
```